Kraft Eco-friendly pouch back imprint

Updating the design imprint on the back of our eco-friendly kraft stand up pouches. The current package back is a story letter but we want to change it to be more visually eye catching and make better use of buzzwords and graphics. I've uploaded a PDF with the current graphic so that key buzz words and thoughts could be pulled and highlighted.

The printing will be done in black and white, so don't spend time with colors. The imprint area is approximately 7" high x 5" wide.

I definitely want our logo at the top of the package, and I'm attaching two options.

Our mission is to be the Healthiest Pet Bakery in the U.S. That needs to be another point of emphasis.

Other potential buzzwords or bullets include:
Artisan Recipes
Simple Ingredients
No corn, wheat, soy, GMOs, or preservatives
Handcrafted
Locally sourced (Pacific NW)
Eco-conscious company
Updates

The system only allowed 24 hours. That is a ridiculously short time window.

Target Market(s)

Pet parents seeking natural, healthy products

Industry/Entity Type

independent pet channel

Colors

Designer to choose only greyscale colors for use in the design.

Requirements
Must have
• Logo, Mission, buzz words, graphics

```html
<!DOCTYPE html>
<html lang="en">
<head>
<meta charset="utf-8">
<title>Biscuit Lane Bakery – Pouch Back</title>
<link href="https://fonts.googleapis.com/css2?family=Outfit:wght@400;500&family=Londrina+Solid:wght@400&display=swap" rel="stylesheet">
<style>
  :root {
    --page: #ffffff;
    --kraft: #d8c3ac;
    --kraft-dark: #c2ae97;
    --ink: #1c1c1c;
    --grey: #6f6a64;
    --hill-light: #b3a696;
    --hill-mid: #8a8178;
    --hill-dark: #55504b;
    --hill-deep: #2f2d2b;
    --kraft-text: #d9c7b2;
  }
  * { box-sizing: border-box; margin: 0; padding: 0; }
  html, body { width: 903px; height: 1200px; overflow: hidden; background: var(--page); }
  body { position: relative; font-family: "Outfit", sans-serif; color: var(--ink); }

  .pouch-back {
    position: absolute; left: 87px; top: 86px; width: 728px; height: 1020px;
    background: var(--kraft); overflow: hidden;
  }
  .abs { position: absolute; }

  /* brand */
  .brand-mark { left: 168px; top: 34px; width: 100px; height: 100px; border-radius: 50%; border: 2px solid var(--grey); }
  .brand-name {
    left: 44px; top: 150px; width: 300px; text-align: center;
    font-weight: 500; font-size: 42px; line-height: 46px; color: var(--ink);
  }

  /* headings */
  .heading-band {
    background: var(--ink); color: var(--kraft-text);
    font-family: "Londrina Solid", sans-serif; font-weight: 400; text-transform: uppercase;
    display: flex; align-items: center; justify-content: center; border-radius: 3px;
  }
  .story-band { left: 393px; top: 65px; width: 287px; height: 76px; font-size: 58px; letter-spacing: 1px; }
  .mission-band { left: 57px; top: 300px; width: 230px; height: 47px; font-size: 38px; }
  .recipes-band { left: 401px; top: 304px; width: 212px; height: 47px; font-size: 38px; }

  .body-copy { font-weight: 500; font-size: 16.5px; line-height: 21.8px; white-space: nowrap; }
  .story-copy { left: 401px; top: 150px; }
  .recipes-copy { left: 396px; top: 362px; }
  .crafted-copy { left: 496px; top: 452px; }
  .sourced-copy { left: 383px; top: 540px; }
  .underline { left: 520px; top: 585px; width: 166px; height: 2px; background: var(--ink); border-radius: 1px; }

  /* placeholders */
  .award-badge { left: 284px; top: 291px; }
  .gmo-badge { left: 608px; top: 269px; }
  .usa-map { left: 43px; top: 354px; width: 313px; height: 214px; }
  .heart-hands { left: 381px; top: 452px; width: 112px; height: 84px; background: var(--kraft-dark); border-radius: 10px; }
  .dot-rule { left: 100px; top: 606px; width: 524px; height: 6px; background: var(--grey); border-radius: 3px; opacity: .8; }

  /* mission copy */
  .mission-text { left: 68px; width: 250px; text-align: center; white-space: nowrap; }
  .mission-lead { top: 352px; font-weight: 500; font-size: 21px; }
  .mission-big {
    top: 394px; font-family: "Londrina Solid", sans-serif; font-size: 44px; line-height: 46px;
    text-transform: uppercase; letter-spacing: 1px;
  }
  .mission-tail { top: 490px; font-weight: 500; font-size: 21px; }

  .closing-copy { left: 0; top: 624px; width: 728px; text-align: center; font-weight: 500; font-size: 16.5px; line-height: 21.8px; white-space: nowrap; }
  .signoff { left: 0; top: 704px; width: 728px; text-align: center; font-weight: 500; font-size: 22px; }

  .farm-scene {
    left: 0; top: 745px; width: 728px; height: 216px;
    background: linear-gradient(180deg,
      var(--kraft) 0%,
      var(--kraft-dark) 28%,
      var(--hill-light) 45%,
      var(--hill-mid) 62%,
      var(--hill-dark) 80%,
      var(--hill-deep) 100%);
  }

  .footer-band {
    left: 0; top: 961px; width: 728px; height: 59px; background: var(--ink);
    color: var(--kraft-text); font-weight: 500; font-size: 19px;
    display: flex; align-items: center; justify-content: center; gap: 12px;
  }
</style>
</head>
<body>
  <main class="pouch-back">
    <div class="abs brand-mark"></div>
    <div class="abs brand-name">Biscuit Lane<br>Bakery</div>

    <h2 class="abs heading-band story-band">Our Story</h2>
    <p class="abs body-copy story-copy">Biscuit Lane Bakery was<br>acquired by a couple in Cedar Cove,<br>WA in 2017 (originally founded<br>in 2004) and who also own and<br>operate two independent pet<br>health food stores.</p>

    <div class="abs usa-map" role="img" aria-label="Outline map of the United States">
      <svg width="313" height="214" viewBox="0 0 313 214"><rect x="6" y="20" width="300" height="170" rx="40" fill="#c7b39c"/></svg>
    </div>
    <h2 class="abs heading-band mission-band">Our Mission</h2>
    <svg class="abs award-badge" width="60" height="78" viewBox="0 0 60 78" role="img" aria-label="Award ribbon badge">
      <circle cx="30" cy="28" r="24" fill="none" stroke="#1c1c1c" stroke-width="2.5"/>
      <polygon points="16,48 8,72 20,66 26,76 30,52" fill="none" stroke="#1c1c1c" stroke-width="2"/>
      <polygon points="44,48 52,72 40,66 34,76 30,52" fill="none" stroke="#1c1c1c" stroke-width="2"/>
    </svg>
    <p class="abs mission-text mission-lead">is to be the</p>
    <p class="abs mission-text mission-big">Healthiest<br>Pet Bakery</p>
    <p class="abs mission-text mission-tail">in the U.S.A.</p>

    <h2 class="abs heading-band recipes-band">Our Recipes</h2>
    <svg class="abs gmo-badge" width="72" height="90" viewBox="0 0 72 90" role="img" aria-label="GMO free badge">
      <ellipse cx="38" cy="42" rx="30" ry="38" fill="none" stroke="#1c1c1c" stroke-width="2.5"/>
    </svg>
    <p class="abs body-copy recipes-copy">are clean and simple with no<br>corn, wheat, soy, sweeteners,<br>genetically modified ingredients,<br>or artificial preservatives.</p>
    <div class="abs heart-hands" role="img" aria-label="Hands forming a heart"></div>
    <p class="abs body-copy crafted-copy">Our treats are hand<br>crafted using only the<br>highest quality human<br>grade ingredients,</p>
    <p class="abs body-copy sourced-copy">which are sourced as locally as<br>possible in the Pacific Northwest.</p>
    <div class="abs underline"></div>

    <div class="abs dot-rule" role="img" aria-label="Decorative dotted divider"></div>
    <p class="abs closing-copy">We focus on the environment and this package reflects our commitment<br>to reducing our carbon pawprint. We hope that your furry friend enjoys<br>our hand-crafted treats as much as we enjoy making them.</p>
    <p class="abs signoff">Your friends @ Biscuit Lane Bakery</p>

    <div class="abs farm-scene" role="img" aria-label="Farm landscape with sun, rolling hills, trees, corn stalks and a farmer carrying a harvest"></div>

    <footer class="abs footer-band">
      <span>www.biscuitlanebakery.com</span><span>|</span><span>Harbor Point, WA</span><span>|</span><span>866-555-BARK</span>
    </footer>
  </main>
</body>
</html>
```